Home Security Company Business Card

Looking for a eye catching business card that is non traditional and stands out but yet still looks professional. It should include all the pertinent information such as name, title, address, telephone, e-mail, website address should definitely stand out and then finally the logo.

Target Market(s)

Residential and Commercial accounts mostly upscale accounts

Industry/Entity Type

Security

Contact Information for Business Card

Name
Title
Address
Office #
Cell #
E-mail
Website

Font styles to use
Serif
Sans Serif

Requirements
Must have
• Logo, two sided color configuration
Nice to have
• You decide
Should not have
• There really aren't any.

```html
<!DOCTYPE html>
<html lang="en">
<head>
<meta charset="utf-8">
<title>Ironvale Protection Group – Business Card</title>
<link rel="stylesheet" href="https://fonts.googleapis.com/css2?family=Open+Sans:wght@400;600;700&display=swap">
<style>
  :root {
    --maroon: #7a1420;
    --maroon-dark: #5e0d16;
    --gold: #e9b93a;
    --gold-soft: #f3d27a;
    --card: #ffffff;
    --bg: #ecebe8;
    --ink: #7a1420;
  }
  * { box-sizing: border-box; margin: 0; padding: 0; }
  html, body { width: 1200px; height: 913px; overflow: hidden; }
  body {
    background: var(--bg);
    font-family: "Open Sans", Arial, sans-serif;
    position: relative;
  }
  .card {
    position: absolute;
    width: 525px;
    height: 300px;
    background: var(--card);
    border-radius: 16px;
    overflow: hidden;
    box-shadow: 0 10px 30px rgba(0,0,0,0.18);
    top: 306px;
  }
  .card--front { left: 50px; }
  .card--back { left: 625px; }

  /* Front */
  .side-band {
    position: absolute; left: 0; top: 0; bottom: 0; width: 46px;
    background: linear-gradient(90deg, var(--maroon-dark), var(--maroon));
  }
  .band-icons {
    position: absolute; left: 0; width: 46px; top: 196px;
    display: flex; flex-direction: column; align-items: center; gap: 7px;
  }
  .band-icons svg { width: 13px; height: 13px; }
  .brand {
    display: flex; align-items: center; gap: 8px;
    color: var(--maroon); font-weight: 700;
  }
  .brand-dot { width: 12px; height: 12px; border-radius: 50%; background: var(--gold); flex: none; }
  .card--front .brand { position: absolute; left: 68px; top: 34px; font-size: 17px; letter-spacing: 0.5px; }
  .person { position: absolute; left: 68px; top: 112px; }
  .person-name { font-size: 26px; font-weight: 700; color: var(--maroon); line-height: 1.1; }
  .person-title { font-size: 15px; color: var(--gold); font-weight: 600; margin-top: 2px; }
  .contact-list {
    position: absolute; left: 68px; top: 188px; list-style: none;
    font-size: 15px; color: var(--ink); line-height: 21px; font-weight: 600;
  }

  /* Back */
  .gold-band {
    position: absolute; right: 0; top: 0; bottom: 0; width: 46px;
    background: linear-gradient(90deg, var(--gold-soft), var(--gold));
  }
  .card--back .brand {
    position: absolute; left: 0; right: 46px; top: 108px;
    justify-content: center; font-size: 26px;
  }
  .card--back .brand-dot { width: 18px; height: 18px; }
  .website {
    position: absolute; left: 0; right: 46px; top: 205px; text-align: center;
    font-size: 16px; font-weight: 700; color: var(--maroon);
  }
</style>
</head>
<body>
  <section class="card card--front" aria-label="Business card front">
    <div class="side-band">
      <div class="band-icons">
        <svg viewBox="0 0 16 16" aria-hidden="true"><path d="M4 1h3l1 4-2 1a9 9 0 0 0 4 4l1-2 4 1v3l-2 2C6 14 2 10 2 3z" fill="var(--gold)"/></svg>
        <svg viewBox="0 0 16 16" aria-hidden="true"><rect x="4" y="1" width="8" height="14" rx="1.5" fill="none" stroke="var(--gold)" stroke-width="1.6"/><circle cx="8" cy="12.5" r="1" fill="var(--gold)"/></svg>
        <svg viewBox="0 0 16 16" aria-hidden="true"><rect x="1" y="3" width="14" height="10" rx="1" fill="none" stroke="var(--gold)" stroke-width="1.6"/><path d="M1.5 4l6.5 5 6.5-5" fill="none" stroke="var(--gold)" stroke-width="1.6"/></svg>
        <svg viewBox="0 0 16 16" aria-hidden="true"><path d="M8 1a5 5 0 0 0-5 5c0 4 5 9 5 9s5-5 5-9a5 5 0 0 0-5-5z" fill="var(--gold)"/><circle cx="8" cy="6" r="1.8" fill="var(--maroon)"/></svg>
      </div>
    </div>
    <div class="brand"><span class="brand-dot"></span>Ironvale Protection Group</div>
    <div class="person">
      <h1 class="person-name">Daniel Whitmore</h1>
      <p class="person-title">Owner</p>
    </div>
    <ul class="contact-list">
      <li>+330 5550-1420</li>
      <li>+330 5550-7781</li>
      <li>info@danielwhitmoremail.com</li>
      <li>42 Harbor Lane Westfield, Ohio 44100</li>
    </ul>
  </section>

  <section class="card card--back" aria-label="Business card back">
    <div class="gold-band"></div>
    <div class="brand"><span class="brand-dot"></span>Ironvale Protection Group</div>
    <p class="website">www.ironvaleprotectiongroup.com</p>
  </section>
</body>
</html>
```